Business Card Design

We are a commercial real estate brokerage in San Francisco, leasing office buildings downtown.
I would like a clean, elegant look. Simple but powerful .

Industry/Entity Type

Business

Contact Information for Business Card

Derek Holloway
lic# 07258143
415.555.0172
derek@velt-commercial.example
velt-commercial.example

```html
<!DOCTYPE html>
<html lang="en">
<head>
<meta charset="utf-8">
<title>Velt Commercial — Business Card</title>
<link rel="stylesheet" href="https://fonts.googleapis.com/css2?family=Arimo:wght@400;700&display=swap">
<style>
  :root {
    --page: #e9eaec;
    --slate-blue: #8493b4;
    --slate-blue-light: #a9b6d2;
    --white: #ffffff;
    --steel: #8c8d90;
    --steel-dark: #77787b;
    --divider: #b9c3db;
    --ink: #3c4250;
  }
  * { box-sizing: border-box; margin: 0; padding: 0; }
  html, body {
    width: 1200px; height: 950px; overflow: hidden;
    background: var(--page);
    font-family: "Arimo", Arial, sans-serif;
  }
  .sheet {
    width: 1200px; height: 950px;
    display: flex; flex-direction: column; align-items: center; justify-content: center;
    gap: 60px;
  }
  .card {
    width: 620px; height: 354px;
    position: relative; overflow: hidden;
    box-shadow: 0 6px 18px rgba(0,0,0,0.18);
  }

  /* Front */
  .card-front {
    background: var(--slate-blue);
    display: flex; flex-direction: column; align-items: center; justify-content: center;
    color: var(--white);
  }
  .brand { display: flex; align-items: center; gap: 16px; }
  .brand-square { width: 22px; height: 22px; background: currentColor; }
  .brand-name {
    font-weight: 700; font-size: 40px; letter-spacing: 2px; line-height: 1;
    text-transform: uppercase;
  }
  .tagline {
    margin-top: 44px; text-align: center;
    font-size: 15px; line-height: 1.4; letter-spacing: 0.3px;
  }

  /* Back */
  .card-back { display: flex; background: var(--white); }
  .back-brand-side {
    width: 47%; display: flex; align-items: center; justify-content: center;
    color: var(--slate-blue);
  }
  .back-brand-side .brand-name { font-size: 28px; }
  .back-brand-side .brand-square { width: 16px; height: 16px; }
  .back-divider { width: 5px; background: var(--divider); }
  .back-contact-side {
    flex: 1;
    background: linear-gradient(160deg, var(--steel) 0%, var(--steel-dark) 100%);
    padding: 70px 0 0 44px; color: var(--white);
  }
  .person-name {
    color: var(--slate-blue-light); font-size: 22px; font-weight: 700; margin-bottom: 10px;
  }
  .contact-list { list-style: none; font-size: 16px; line-height: 1.75; }
  .contact-item { display: flex; align-items: center; gap: 10px; }
  .contact-icon { width: 16px; height: 16px; flex: none; }
  .license { margin-bottom: 4px; }
</style>
</head>
<body>
<main class="sheet">
  <section class="card card-front" aria-label="Card front">
    <div class="brand">
      <span class="brand-square"></span>
      <span class="brand-name">Velt Commercial</span>
    </div>
    <p class="tagline">commercial real estate brokerage in San Francisco<br>leasing office buildings downtown.</p>
  </section>

  <section class="card card-back" aria-label="Card back">
    <div class="back-brand-side">
      <div class="brand">
        <span class="brand-square"></span>
        <span class="brand-name">Velt Commercial</span>
      </div>
    </div>
    <div class="back-divider"></div>
    <div class="back-contact-side">
      <h1 class="person-name">Derek Holloway</h1>
      <p class="license contact-list">lic# 07258143</p>
      <ul class="contact-list">
        <li class="contact-item">
          <svg class="contact-icon" viewBox="0 0 16 16" fill="#fff"><path d="M3.5 1.5l2.5 3-1.5 1.5c.8 1.8 2.2 3.2 4 4l1.5-1.5 3 2.5-1.5 2.5C6.8 13.5 2.5 9.2 1 4z"/></svg>
          <span>415.555.0172</span>
        </li>
        <li class="contact-item">
          <svg class="contact-icon" viewBox="0 0 16 16"><rect x="1" y="3" width="14" height="10" fill="#fff"/><path d="M1 3l7 5.5L15 3" fill="none" stroke="#808184" stroke-width="1.2"/></svg>
          <span>derek@velt-commercial.example</span>
        </li>
        <li class="contact-item">
          <svg class="contact-icon" viewBox="0 0 16 16" fill="none" stroke="#fff" stroke-width="1.3"><circle cx="8" cy="8" r="6.5"/><ellipse cx="8" cy="8" rx="2.8" ry="6.5"/><path d="M1.5 8h13"/></svg>
          <span>velt-commercial.example</span>
        </li>
      </ul>
    </div>
  </section>
</main>
</body>
</html>
```